Design a New Business Card for Our Company

We are looking for fresh, unique, and a modern business card that reflects our roots as digital marketing agency focused on SEM.

Industry/Entity Type

Marketing

Contact Information for Business Card

looking for very unique out of the box designs. clean and modern that compliments our logo

Requirements
Must have
• colors should match our logo
• Front should have name, address, email, and phone/fax of the person, phone/fax are the same number
• back should have our url

```html
<!DOCTYPE html>
<html lang="en">
<head>
<meta charset="utf-8">
<title>Brightpath Media — Business Card</title>
<link href="https://fonts.googleapis.com/css2?family=Source+Sans+3:wght@400;600;700&display=swap" rel="stylesheet">
<style>
  :root {
    --stage: #4a4a4a;
    --card-white: #ffffff;
    --brand-blue: #5e97d0;
    --name-grey: #9b9b9b;
    --text-dark: #4f4f4f;
    --icon-grey: #8c8c8c;
    --divider: #c9c9c9;
    --on-blue: #ffffff;
  }
  * { box-sizing: border-box; margin: 0; padding: 0; }
  html, body { width: 1105px; height: 1200px; overflow: hidden; }
  body {
    background: var(--stage);
    font-family: "Source Sans 3", "Helvetica Neue", Arial, sans-serif;
    position: relative;
  }
  .card {
    position: absolute;
    left: 196px;
    width: 720px;
    height: 412px;
  }
  .card-front { top: 146px; background: var(--card-white); }
  .card-back  { top: 602px; background: var(--brand-blue); }

  .brand {
    position: absolute;
    left: 0; right: 0;
    display: flex;
    align-items: center;
    justify-content: center;
    gap: 12px;
    height: 60px;
  }
  .brand-dot {
    width: 30px; height: 30px;
    border-radius: 50%;
  }
  .brand-name {
    font-size: 46px;
    font-weight: 700;
    letter-spacing: -0.5px;
    line-height: 1;
  }
  .card-front .brand { top: 100px; }
  .card-front .brand-dot { background: var(--brand-blue); }
  .card-front .brand-name { color: var(--brand-blue); }
  .card-back .brand { top: 178px; }
  .card-back .brand-dot { background: var(--on-blue); }
  .card-back .brand-name { color: var(--on-blue); }

  .person {
    position: absolute;
    right: 426px;
    top: 248px;
    text-align: right;
  }
  .person-name {
    font-size: 25px;
    font-weight: 600;
    color: var(--name-grey);
    line-height: 1.2;
  }
  .person-title {
    font-size: 19px;
    color: var(--brand-blue);
    line-height: 1.3;
  }
  .divider {
    position: absolute;
    left: 319px;
    top: 208px;
    width: 1px;
    height: 138px;
    background: var(--divider);
  }
  .contact {
    position: absolute;
    left: 343px;
    top: 207px;
    font-size: 19px;
    color: var(--text-dark);
    line-height: 26px;
    list-style: none;
  }
  .contact-address { margin-bottom: 6px; }
  .contact-line {
    display: flex;
    align-items: center;
    gap: 8px;
    height: 28px;
  }
  .contact-line svg { width: 18px; height: 18px; fill: var(--icon-grey); flex: none; }

  .web-address {
    position: absolute;
    left: 0; right: 0;
    top: 346px;
    text-align: center;
    color: var(--on-blue);
    font-size: 18px;
    letter-spacing: 3.5px;
  }
</style>
</head>
<body>
  <section class="card card-front" aria-label="Business card front">
    <div class="brand">
      <span class="brand-dot"></span>
      <span class="brand-name">brightpath media</span>
    </div>

    <div class="person">
      <p class="person-name">Corin Ashdale</p>
      <p class="person-title">CEO/Founder</p>
    </div>

    <div class="divider"></div>

    <ul class="contact">
      <li class="contact-address">1420 Harbor View Road<br>Juneau, Alaska 99801</li>
      <li class="contact-line">
        <svg viewBox="0 0 24 24" aria-hidden="true"><path d="M6.6 10.8a15.1 15.1 0 0 0 6.6 6.6l2.2-2.2c.3-.3.7-.4 1-.2 1.1.4 2.3.6 3.6.6.6 0 1 .4 1 1V20c0 .6-.4 1-1 1A17 17 0 0 1 3 4c0-.6.4-1 1-1h3.5c.6 0 1 .4 1 1 0 1.3.2 2.5.6 3.6.1.3 0 .7-.2 1l-2.3 2.2z"/></svg>
        555 214 7730
      </li>
      <li class="contact-line">
        <svg viewBox="0 0 24 24" aria-hidden="true"><path d="M6 2h12v6H6zM3 9h18a1 1 0 0 1 1 1v7h-4v5H6v-5H2v-7a1 1 0 0 1 1-1zm5 7v4h8v-4z"/></svg>
        555 214 7731
      </li>
      <li class="contact-line">
        <svg viewBox="0 0 24 24" aria-hidden="true"><path d="M2 5h20v14H2zm2 2v.4l8 5 8-5V7z"/></svg>
        corin@brightpathmedia.com
      </li>
    </ul>
  </section>

  <section class="card card-back" aria-label="Business card back">
    <div class="brand">
      <span class="brand-dot"></span>
      <span class="brand-name">brightpath media</span>
    </div>
    <p class="web-address">www.brightpathmedia.com</p>
  </section>
</body>
</html>
```